Need Flyer for Our Real estate Agency

Need to run General Campaign for our agency with Start of New Year as our theme ..Must have an agent's picture on the DL..
Address:
27 / 486Brindle rd, Marsden VIC 3047
Ph:03 9412 7306
email:info@kovalinrealestate.com.au
www.kovalinrealestate.com.au
Something like as attached picture..
Target Market(s)
Home Buyers
Industry/Entity Type
Real Estate Agent
Requirements
Must have
- Our Logo Colours

```html
<!DOCTYPE html>
<html lang="en">
<head>
<meta charset="utf-8">
<title>Kovalin Real Estate – New Year DL Flyer</title>
<link rel="stylesheet" href="https://fonts.googleapis.com/css2?family=Cabin:wght@400;500;700&family=Open+Sans:wght@400;600;700&display=swap">
<style>
  :root {
    --page: #e9e9eb;
    --navy: #14285f;
    --navy-deep: #0b1a48;
    --navy-light: #1f3a86;
    --wine: #7a1520;
    --silver: #c9cacd;
    --white: #ffffff;
    --photo-sky: #9fb4cf;
    --photo-house: #8d8f93;
    --photo-suit: #26365e;
    --photo-hands: #d9b9a4;
    --photo-model: #c94a47;
  }
  * { box-sizing: border-box; margin: 0; padding: 0; }
  html, body { width: 1192px; height: 1200px; overflow: hidden; }
  body {
    background: var(--page);
    font-family: "Cabin", "Gill Sans", sans-serif;
    color: var(--white);
    position: relative;
  }
  .flyer {
    position: absolute;
    left: 96px;
    width: 1000px;
    height: 476px;
    overflow: hidden;
    box-shadow: 0 6px 18px rgba(0,0,0,0.18);
  }
  .flyer--front { top: 88px; }
  .flyer--back { top: 636px; }
  .flyer__art { position: absolute; inset: 0; width: 100%; height: 100%; }

  .brand {
    position: absolute;
    display: flex;
    align-items: center;
    gap: 14px;
    font-family: "Cabin", sans-serif;
    font-weight: 500;
    font-size: 60px;
    letter-spacing: 6px;
    color: var(--white);
    line-height: 1;
  }
  .brand__mark { width: 16px; height: 16px; background: var(--white); }

  .flyer--front .brand { left: 273px; top: 150px; transform: translateX(-50%); }
  .headline {
    position: absolute;
    left: 273px; top: 222px;
    transform: translateX(-50%);
    width: 460px;
    text-align: center;
    font-weight: 400;
    font-size: 34px;
    line-height: 1.32;
  }
  .subline {
    position: absolute;
    left: 273px; top: 338px;
    transform: translateX(-50%);
    white-space: nowrap;
    font-family: "Open Sans", sans-serif;
    font-size: 15.5px;
    text-transform: uppercase;
  }
  .subline strong { font-weight: 700; }
  .call-pill {
    position: absolute;
    left: 86px; top: 382px;
    width: 378px; height: 50px;
    border-radius: 25px;
    background: var(--white);
    box-shadow: 0 3px 6px rgba(0,0,0,0.3);
    display: flex; align-items: center; justify-content: center; gap: 10px;
    font-family: "Open Sans", sans-serif;
    font-weight: 700;
    font-size: 22px;
    color: var(--wine);
    white-space: nowrap;
  }
  .call-pill svg { width: 22px; height: 22px; }
  .appraisal {
    position: absolute;
    left: 273px; top: 440px;
    transform: translateX(-50%);
    font-size: 18px;
    white-space: nowrap;
  }

  .flyer--back .brand { left: 727px; top: 140px; transform: translateX(-50%); }
  .agent-name {
    position: absolute;
    left: 574px; top: 226px;
    font-size: 23px;
  }
  .contact-list {
    position: absolute;
    left: 574px; top: 272px;
    list-style: none;
    font-size: 19px;
  }
  .contact-list li { display: flex; align-items: center; gap: 12px; height: 37px; }
  .contact-list svg { width: 18px; height: 18px; flex: none; }
  .office-address {
    position: absolute;
    left: 510px; top: 428px;
    font-size: 20px;
    white-space: nowrap;
  }
</style>
</head>
<body>

<section class="flyer flyer--front" aria-label="Flyer front">
  <svg class="flyer__art" viewBox="0 0 1000 476" preserveAspectRatio="none">
    <defs>
      <linearGradient id="navyFront" x1="0" y1="0" x2="1" y2="0">
        <stop offset="0" stop-color="var(--navy-deep)"/>
        <stop offset="0.6" stop-color="var(--navy-light)"/>
        <stop offset="1" stop-color="var(--navy)"/>
      </linearGradient>
      <linearGradient id="agentPhoto" x1="0" y1="0" x2="0" y2="1">
        <stop offset="0" stop-color="var(--photo-sky)"/>
        <stop offset="0.45" stop-color="var(--photo-house)"/>
        <stop offset="1" stop-color="var(--photo-suit)"/>
      </linearGradient>
    </defs>
    <rect width="1000" height="476" fill="url(#navyFront)"/>
    <rect x="0" y="404" width="640" height="72" fill="var(--wine)"/>
    <rect x="0" y="401" width="640" height="3" fill="var(--white)"/>
    <path d="M640 0 L700 0 Q560 240 620 476 L600 476 Q515 220 640 0 Z" fill="var(--silver)"/>
    <g role="img" aria-label="Photo of the sales agent in a suit standing in front of a two-storey family home">
      <path d="M700 0 L1000 0 L1000 476 L620 476 Q560 240 700 0 Z" fill="url(#agentPhoto)"/>
    </g>
    <path d="M700 0 Q560 240 620 476" fill="none" stroke="var(--white)" stroke-width="5"/>
  </svg>

  <div class="brand"><span class="brand__mark"></span>KOVALIN</div>
  <h1 class="headline">Curios to know what your home is worth?</h1>
  <p class="subline">Start of new year with <strong>Devan Mehra</strong> and find out!</p>
  <div class="call-pill">
    <span>CALL ME NOW!</span>
    <svg viewBox="0 0 24 24" aria-hidden="true"><circle cx="12" cy="12" r="10.5" fill="none" stroke="currentColor" stroke-width="2"/><path d="M8.5 7c.6-.5 1.3-.4 1.6.2l.9 1.8c.2.5.1 1-.3 1.3l-.6.5c.6 1.3 1.6 2.3 2.9 2.9l.5-.6c.3-.4.9-.5 1.3-.3l1.8.9c.6.3.7 1 .2 1.6-.9 1-2.2 1.3-3.5.6-2.2-1.1-4-2.9-5.1-5.1-.6-1.3-.4-2.6.3-3.8z" fill="currentColor"/></svg>
    <span>03 9412 7306</span>
  </div>
  <p class="appraisal">For Free property Appraisal</p>
</section>

<section class="flyer flyer--back" aria-label="Flyer back">
  <svg class="flyer__art" viewBox="0 0 1000 476" preserveAspectRatio="none">
    <defs>
      <linearGradient id="navyBack" x1="0" y1="0" x2="1" y2="0">
        <stop offset="0" stop-color="var(--navy-light)"/>
        <stop offset="0.5" stop-color="var(--navy)"/>
        <stop offset="1" stop-color="var(--navy-deep)"/>
      </linearGradient>
      <radialGradient id="handsPhoto" cx="0.45" cy="0.55" r="0.7">
        <stop offset="0" stop-color="var(--photo-model)"/>
        <stop offset="0.35" stop-color="var(--photo-hands)"/>
        <stop offset="1" stop-color="var(--photo-suit)"/>
      </radialGradient>
    </defs>
    <rect width="1000" height="476" fill="url(#navyBack)"/>
    <rect x="380" y="406" width="620" height="70" fill="var(--wine)"/>
    <rect x="380" y="403" width="620" height="3" fill="var(--white)"/>
    <path d="M330 0 L420 0 Q510 240 414 476 L400 476 Q470 260 330 0 Z" fill="var(--silver)"/>
    <g role="img" aria-label="Photo of two hands sheltering a small red model house">
      <path d="M0 0 L330 0 Q470 260 400 476 L0 476 Z" fill="url(#handsPhoto)"/>
    </g>
    <path d="M330 0 Q470 260 400 476" fill="none" stroke="var(--white)" stroke-width="5"/>
  </svg>

  <div class="brand"><span class="brand__mark"></span>KOVALIN</div>
  <p class="agent-name">Devan Mehra, Sales Manager</p>
  <ul class="contact-list">
    <li>
      <svg viewBox="0 0 24 24" aria-hidden="true"><circle cx="12" cy="12" r="10.5" fill="none" stroke="currentColor" stroke-width="2"/><path d="M8.5 7c.6-.5 1.3-.4 1.6.2l.9 1.8c.2.5.1 1-.3 1.3l-.6.5c.6 1.3 1.6 2.3 2.9 2.9l.5-.6c.3-.4.9-.5 1.3-.3l1.8.9c.6.3.7 1 .2 1.6-.9 1-2.2 1.3-3.5.6-2.2-1.1-4-2.9-5.1-5.1-.6-1.3-.4-2.6.3-3.8z" fill="currentColor"/></svg>
      0431 728 519
    </li>
    <li>
      <svg viewBox="0 0 24 24" aria-hidden="true"><circle cx="12" cy="12" r="10.5" fill="none" stroke="currentColor" stroke-width="2"/><rect x="6.5" y="8" width="11" height="8" fill="currentColor"/><path d="M6.5 8 L12 12.5 L17.5 8" fill="none" stroke="var(--navy)" stroke-width="1.3"/></svg>
      devan.mehra@kovalinrealestate.com.au
    </li>
    <li>
      <svg viewBox="0 0 24 24" aria-hidden="true"><circle cx="12" cy="12" r="10.5" fill="none" stroke="currentColor" stroke-width="2"/><circle cx="12" cy="12" r="6" fill="none" stroke="currentColor" stroke-width="1.3"/><ellipse cx="12" cy="12" rx="2.6" ry="6" fill="none" stroke="currentColor" stroke-width="1.3"/><path d="M6 12 H18" stroke="currentColor" stroke-width="1.3"/></svg>
      www.kovalinrealestate.com.au
    </li>
  </ul>
  <p class="office-address">27/486 Brindle Rd Marsden, Victoria, Australia 3047</p>
</section>

</body>
</html>
```